Velora Entertainment

Logo for business card design

Target Market(s)

potential film investors and screenwriters

Industry/Entity Type

Business

Contact Information for Business Card

as shown, website here is a placeholder position

Requirements
Must have
• great visual appeal
Nice to have
• harmony of colors; must evoke spirit of
• U.S.-China cooperation

```html
<!DOCTYPE html>
<html lang="en">
<head>
<meta charset="utf-8">
<title>Velora Entertainment – Business Card</title>
<link rel="stylesheet" href="https://fonts.googleapis.com/css2?family=Source+Sans+3:wght@400;600;700&display=swap">
<style>
  :root {
    --backdrop: #9b9c9e;
    --card-front: #f4f4f5;
    --card-back-top: #8d8e90;
    --card-back-bottom: #7b7c7e;
    --brand-red: #c8101a;
    --brand-yellow: #e0c000;
    --brand-navy: #16167a;
    --ink: #1d1d1f;
    --divider: #8a8a8a;
    --logo-light: #e9eef2;
  }
  * { box-sizing: border-box; margin: 0; padding: 0; }
  html, body {
    width: 1105px; height: 1200px; overflow: hidden;
    background: var(--backdrop);
    font-family: "Source Sans 3", "Segoe UI", sans-serif;
  }
  .card {
    position: absolute;
    left: 179px;
    width: 747px;
    height: 427px;
  }
  .card-front { top: 119px; background: var(--card-front); }
  .card-back {
    top: 636px;
    background: linear-gradient(180deg, var(--card-back-top), var(--card-back-bottom));
  }

  .wordmark {
    position: absolute;
    display: flex;
    align-items: center;
    gap: 14px;
  }
  .wordmark-square {
    width: 46px; height: 46px;
    background: var(--brand-red);
    flex: none;
  }
  .wordmark-name {
    font-weight: 700;
    font-size: 31px;
    line-height: 1.05;
    color: var(--brand-navy);
    letter-spacing: 0.5px;
  }
  .card-front .wordmark { left: 78px; top: 176px; }
  .card-back .wordmark { left: 50%; top: 50%; transform: translate(-50%, -50%); }
  .card-back .wordmark-name { color: var(--logo-light); }

  .divider {
    position: absolute;
    left: 388px; top: 81px;
    width: 1px; height: 253px;
    background: var(--divider);
  }

  .contact {
    position: absolute;
    left: 427px; top: 72px;
    color: var(--ink);
  }
  .contact-name {
    font-size: 26px; font-weight: 600;
    color: var(--brand-red);
    line-height: 1.15;
  }
  .contact-role {
    font-size: 20px;
    color: var(--brand-navy);
    line-height: 1.2;
    margin-bottom: 22px;
  }
  .contact-address {
    font-size: 19px; line-height: 1.4;
    font-style: normal;
    margin-bottom: 8px;
  }
  .contact-list { list-style: none; }
  .contact-list li {
    display: flex; align-items: center; gap: 12px;
    font-size: 19px; line-height: 29px;
  }
  .contact-list svg { width: 17px; height: 17px; fill: var(--brand-red); flex: none; }

  .stripe-band {
    position: absolute;
    left: 0; bottom: 0;
    width: 100%; height: 24px;
    display: flex; gap: 3px;
  }
  .stripe { flex: 1; }
  .stripe-red { background: var(--brand-red); }
  .stripe-yellow { background: var(--brand-yellow); }
  .stripe-navy { background: var(--brand-navy); }
</style>
</head>
<body>

<section class="card card-front" aria-label="Business card front">
  <div class="wordmark">
    <span class="wordmark-square"></span>
    <span class="wordmark-name">Velora<br>Entertainment</span>
  </div>

  <div class="divider"></div>

  <div class="contact">
    <p class="contact-name">Marcus Hale</p>
    <p class="contact-role">CEO/Founder</p>
    <address class="contact-address">4120 Cedar Ridge Road<br>Juneau, Alaska 99801</address>
    <ul class="contact-list">
      <li>
        <svg viewBox="0 0 24 24" aria-hidden="true"><path d="M6.6 10.8a15.1 15.1 0 0 0 6.6 6.6l2.2-2.2c.3-.3.7-.4 1-.2 1.1.4 2.3.6 3.6.6.6 0 1 .4 1 1V20c0 .6-.4 1-1 1C10.6 21 3 13.4 3 4c0-.6.4-1 1-1h3.5c.6 0 1 .4 1 1 0 1.3.2 2.5.6 3.6.1.3 0 .7-.2 1z"/></svg>
        <span>907 512 3380</span>
      </li>
      <li>
        <svg viewBox="0 0 24 24" aria-hidden="true"><path d="M7 1h10a2 2 0 0 1 2 2v18a2 2 0 0 1-2 2H7a2 2 0 0 1-2-2V3a2 2 0 0 1 2-2zm0 3v14h10V4zm5 15.2a1.2 1.2 0 1 0 0 2.4 1.2 1.2 0 0 0 0-2.4z"/></svg>
        <span>907 644 1297</span>
      </li>
      <li>
        <svg viewBox="0 0 24 24" aria-hidden="true"><path d="M2 5h20v14H2zm2 2v.5l8 5 8-5V7zm0 2.8V17h16V9.8l-8 5z"/></svg>
        <span>hello@veloraent.com</span>
      </li>
      <li>
        <svg viewBox="0 0 24 24" aria-hidden="true"><path d="M12 2a10 10 0 1 0 0 20 10 10 0 0 0 0-20zm-1 17.9A8 8 0 0 1 4.2 10l4.8 4.8v1a2 2 0 0 0 2 2zm6.9-2.5a2 2 0 0 0-1.9-1.4h-1v-3a1 1 0 0 0-1-1H8v-2h2a1 1 0 0 0 1-1V7h2a2 2 0 0 0 2-2v-.4a8 8 0 0 1 2.9 12.8z"/></svg>
        <span>www.veloraent.com</span>
      </li>
    </ul>
  </div>

  <div class="stripe-band">
    <span class="stripe stripe-red"></span>
    <span class="stripe stripe-yellow"></span>
    <span class="stripe stripe-navy"></span>
  </div>
</section>

<section class="card card-back" aria-label="Business card back">
  <div class="wordmark">
    <span class="wordmark-square"></span>
    <span class="wordmark-name">Velora<br>Entertainment</span>
  </div>
</section>

</body>
</html>
```